CLEARLINE™ by VESKO GOLF Squarespace website design

I am looking to have the website look and feel designed. I will attach all the initial content and some other sites I like for inspiration. https://www.fairwaysensa.com/ https://quillstrike.com/
This is the top bar nav
CLEARLINE™ by VESKO GOLF logo
Center: Home | Process | Technology | The Fit | Stroke Print | Testimonials | About
Right: [Start My Fitting] (gold CTA button)

Target Market(s)

Upscale Golfers

Industry/Entity Type

Golf and Technology

```html
<!DOCTYPE html>
<html lang="en">
<head>
<meta charset="utf-8">
<title>CLEARLINE™ by VESKO GOLF</title>
<link rel="stylesheet" href="https://fonts.googleapis.com/css2?family=Michroma&family=Montserrat:wght@400;500;600;700&display=swap">
<style>
:root{
  --gold:#ffd400;
  --black:#000;
  --ink:#0b0b10;
  --panel:#0c0c13;
  --grey:#7a7a7a;
  --white:#fff;
  --muted:#d9d9d9;
}
*{box-sizing:border-box;margin:0;padding:0}
html,body{width:1200px;height:3184px;overflow:hidden;background:var(--black)}
body{position:relative;font-family:"Montserrat",sans-serif;color:var(--white)}
.display{font-family:"Michroma",sans-serif;font-variant:small-caps;color:var(--gold);letter-spacing:.06em}
.abs{position:absolute}
.btn{position:absolute;display:flex;align-items:center;justify-content:center;background:var(--gold);color:#000;border-radius:30px;font-family:"Michroma",sans-serif;font-variant:small-caps;font-size:15px;letter-spacing:.12em;text-decoration:none}

/* hero */
.hero{position:absolute;left:0;top:0;width:1200px;height:671px;background:#050505;overflow:hidden}
.hero-photo{position:absolute;left:520px;top:0;width:680px;height:671px;
  background:radial-gradient(circle at 70% 35%,#b32020 0,#7a1515 18%,transparent 38%),
  linear-gradient(90deg,#050505 0,#3a3a40 35%,#8b8f99 70%,#c9c3bc 100%)}
.hero-shade{position:absolute;inset:0;background:linear-gradient(90deg,#000 0,rgba(0,0,0,.85) 40%,rgba(0,0,0,0) 70%)}
.brand{position:absolute;left:35px;top:30px;display:flex;align-items:center;gap:10px}
.brand-dot{width:22px;height:22px;border-radius:50%;background:var(--gold)}
.brand-name{font-family:"Montserrat",sans-serif;font-weight:700;font-size:20px;line-height:1;color:var(--white);letter-spacing:.02em}
.brand-sub{font-weight:700;font-size:8px;letter-spacing:.3em;color:var(--white);margin-top:3px}
.nav{position:absolute;left:310px;top:37px;display:flex;gap:16px;font-size:16px;font-weight:500}
.nav a{color:var(--white);text-decoration:none}
.nav a.active{color:var(--gold)}
.hero h1{position:absolute;left:100px;width:640px;top:140px;text-align:center;font-size:38px;line-height:44px}
.hero .lead{position:absolute;left:100px;width:640px;top:243px;text-align:center;font-size:14px;font-weight:600;line-height:26.5px}
.hero .body{position:absolute;left:110px;width:620px;top:344px;text-align:center;font-size:12.5px;line-height:26.5px}
.hero .note{position:absolute;left:100px;width:640px;top:600px;text-align:center;font-size:12.5px}

/* why */
.why{position:absolute;left:0;top:671px;width:1200px;height:817px;background:#000;overflow:hidden}
.why-photo{position:absolute;left:700px;top:250px;width:500px;height:567px;
  background:radial-gradient(ellipse at 40% 60%,#4a3a10 0,#1b1608 35%,transparent 70%)}
.why h2{position:absolute;left:0;width:1200px;top:70px;text-align:center;font-size:36px}
.why .sub{position:absolute;left:0;width:1200px;top:128px;text-align:center;font-size:18px;font-weight:500}
.feat h3{font-family:"Michroma",sans-serif;font-variant:small-caps;color:var(--gold);font-size:13px;letter-spacing:.15em;line-height:24px;font-weight:400}
.feat p{font-size:15px;line-height:22.5px;font-weight:500;margin-top:10px}
.icon{position:absolute;width:74px;height:74px;border-radius:50%;background:var(--grey);display:flex;align-items:center;justify-content:center}
.ring{position:absolute;left:409px;top:337px;width:380px;height:290px;border:3px solid rgba(255,212,0,.35);border-radius:50%}

/* process */
.process{position:absolute;left:0;top:1488px;width:1200px;height:665px;overflow:hidden;
  background:radial-gradient(ellipse at 50% 40%,#3a3a3a 0,#222 45%,#141414 100%)}
.process h2{position:absolute;left:0;width:1200px;top:88px;text-align:center;font-size:36px}
.step{position:absolute;top:197px;width:312px;height:312px;border-radius:50%;background:var(--grey);border:4px solid var(--gold);text-align:center}
.step .num{font-family:"Montserrat",sans-serif;font-weight:500;font-size:38px;margin-top:40px}
.step .mark{width:60px;height:4px;background:var(--gold);margin:14px auto 36px;border-radius:2px}
.step h3{font-family:"Michroma",sans-serif;font-variant:small-caps;font-weight:400;font-size:14px;letter-spacing:.15em}
.step p{font-size:13.5px;color:#e6e6e6;line-height:20px;margin:12px auto 0;width:200px}

/* testimonials */
.results{position:absolute;left:0;top:2153px;width:1200px;height:633px;background:#000;overflow:hidden}
.results h2{position:absolute;left:111px;top:66px;font-size:36px}
.results .sub{position:absolute;left:111px;top:126px;font-size:18px;font-weight:500}
.arrow{position:absolute;top:64px;width:56px;height:56px;border-radius:50%;background:#3a3000;display:flex;align-items:center;justify-content:center;color:#6b5a00;font-size:22px;font-weight:700}
.card{position:absolute;width:303px;height:360px;border-radius:24px;background:var(--panel);padding:26px 26px}
.stars{color:var(--gold);font-size:22px;letter-spacing:6px}
.card p{font-size:14.5px;line-height:22.3px;margin-top:14px}
.who{position:absolute;left:26px;bottom:62px;color:var(--gold);font-weight:600;font-size:17px}
.avatar{position:absolute;right:30px;bottom:26px;width:82px;height:82px;border-radius:50%;background:linear-gradient(160deg,#c9c9c9,#3a3d44)}

/* cta */
.cta{position:absolute;left:0;top:2786px;width:1200px;height:341px;background:#0e0e0e}
.cta h2{position:absolute;left:0;width:1200px;top:70px;text-align:center;font-size:36px}
.cta .sub{position:absolute;left:0;width:1200px;top:133px;text-align:center;font-size:18px;font-weight:500}
.cta .tag{position:absolute;left:0;width:1200px;top:283px;text-align:center;font-family:"Michroma",sans-serif;font-variant:small-caps;font-size:14px;letter-spacing:.14em}
.footer{position:absolute;left:0;top:3127px;width:1200px;height:57px;background:#000;text-align:center;font-size:14.5px;line-height:57px}
</style>
</head>
<body>

<section class="hero">
  <div class="hero-photo" role="img" aria-label="Golfer in a red shirt finishing a driver swing in front of a blurred crowd"></div>
  <div class="hero-shade"></div>
  <div class="brand">
    <span class="brand-dot"></span>
    <div><div class="brand-name">CLEARLINE™</div><div class="brand-sub">BY VESKO GOLF</div></div>
  </div>
  <nav class="nav">
    <a class="active" href="#">Home</a><a href="#">Process</a><a href="#">Technology</a><a href="#">The Fit</a><a href="#">Stroke Print</a><a href="#">Testimonials</a><a href="#">About</a>
  </nav>
  <a class="btn" href="#" style="left:963px;top:23px;width:199px;height:46px;font-size:14px">Start My Fitting</a>
  <h1 class="display">Your Swing<br>Perfected by AI.</h1>
  <p class="lead">Welcome to Clearline™ by VESKO Golf — the world's first fully automated, AI-powered club-fitting system that engineers your perfect bag from data, not guesswork. No appointments. No bias. Just precision built for performance.</p>
  <p class="body">Every golfer's swing is unique — and so should be every club in your bag. Clearline's AI engine analyzes your swing data, tempo, and ball-flight tendencies, running millions of potential combinations of heads, shafts, and grips across all major OEMs. It isolates the setup that maximizes your distance, consistency, and dispersion — a mathematically optimized build designed for your exact Stroke Print. From driver to putter, every recommendation is powered by data — not opinion.</p>
  <a class="btn" href="#" style="left:287px;top:533px;width:266px;height:46px">Start Your AI Fitting</a>
  <p class="note">No payment required. Receive your personalized Stroke Print Report instantly.</p>
</section>

<section class="why">
  <div class="why-photo" role="img" aria-label="Golf iron resting behind a ball with a glowing swing arc"></div>
  <h2 class="display">Why Clearline</h2>
  <p class="sub">AI Fitting Built for Golfers Who Expect Proof.</p>
  <div class="ring"></div>

  <div class="feat abs" style="left:450px;width:300px;top:192px;text-align:center">
    <h3>Millions<br>of simulations</h3>
    <p>Every major OEM modeled — shafts, lofts, grips, and geometry.</p>
  </div>
  <div class="feat abs" style="left:100px;width:250px;top:301px;text-align:right">
    <h3>Smarter<br>than human fitting</h3>
    <p>Machine learning, biomechanics, and physics replace guesswork.</p>
  </div>
  <div class="feat abs" style="left:851px;width:250px;top:301px;text-align:left">
    <h3>Faster<br>than a session</h3>
    <p>Every major OEM modeled — shafts, lofts, grips, and geometry.</p>
  </div>
  <div class="feat abs" style="left:450px;width:300px;top:672px;text-align:center">
    <h3>Portable confidence</h3>
    <p style="margin-top:8px">Your Stroke Print Report travels with you to any builder.</p>
  </div>

  <div class="icon" style="left:372px;top:300px">
    <svg width="40" height="40" viewBox="0 0 40 40" fill="none" stroke="#fff" stroke-width="2"><circle cx="20" cy="13" r="7"/><path d="M7 36c1-9 6-13 13-13s12 4 13 13z"/></svg>
  </div>
  <div class="icon" style="left:562px;top:330px">
    <svg width="40" height="40" viewBox="0 0 40 40" fill="none" stroke="#fff" stroke-width="2"><rect x="5" y="6" width="30" height="21" rx="2"/><path d="M15 34h10M20 27v7M14 16l6-4 6 4v6l-6 3-6-3z"/></svg>
  </div>
  <div class="icon" style="left:746px;top:300px">
    <svg width="40" height="40" viewBox="0 0 40 40" fill="none" stroke="#fff" stroke-width="2"><circle cx="20" cy="22" r="13"/><path d="M17 5h6M20 9v-4M20 22l6-6"/></svg>
  </div>
  <div class="icon" style="left:562px;top:581px">
    <svg width="40" height="40" viewBox="0 0 40 40" fill="none" stroke="#fff" stroke-width="2"><rect x="5" y="6" width="18" height="13" rx="1"/><rect x="17" y="22" width="18" height="12" rx="1"/><path d="M28 10h4v8M12 23v7h3"/></svg>
  </div>
</section>

<section class="process">
  <div class="abs" role="img" aria-label="Dimmed close-up of a golfer gripping a club" style="inset:0;background:radial-gradient(ellipse at 60% 30%,rgba(90,90,90,.5),transparent 60%)"></div>
  <h2 class="display">How It Works</h2>
  <div class="step" style="left:112px">
    <div class="num">01</div><div class="mark"></div>
    <h3>Input Your Stroke Print</h3>
    <p>Tempo, distances, and goals.</p>
  </div>
  <div class="step" style="left:445px">
    <div class="num">02</div><div class="mark"></div>
    <h3>AI Simulation Engine</h3>
    <p>Millions of builds tested in seconds.</p>
  </div>
  <div class="step" style="left:776px">
    <div class="num">03</div><div class="mark"></div>
    <h3>Get Your Report</h3>
    <p>Specs and gapping optimized for your game.</p>
  </div>
  <a class="btn" href="#" style="left:466px;top:565px;width:267px;height:44px;font-size:14px">See the Process</a>
</section>

<section class="results">
  <h2 class="display">Real Golfers Real Results</h2>
  <p class="sub">Validated by data. Proven on the course.</p>
  <div class="arrow" style="left:959px">«</div>
  <div class="arrow" style="left:1029px">»</div>

  <article class="card" style="left:109px;top:168px">
    <div class="stars">★★★★☆</div>
    <p>Lorem ipsum dolor sit amet, consectetur adipiscing elit, sed do eiusmod tempor incididunt ut labore et dolore magna aliqua. Ut enim ad minim veniam, quis nostrud exercitation ullamco laboris nisi ut aliquip ex ea commodo consequat. Duis aute</p>
    <div class="who">Sarah M., Denver</div>
    <div class="avatar" role="img" aria-label="Customer portrait"></div>
  </article>
  <article class="card" style="left:452px;top:220px">
    <div class="stars">★★★★☆</div>
    <p>Lorem ipsum dolor sit amet, consectetur adipiscing elit, sed do eiusmod tempor incididunt ut labore et dolore magna aliqua. Ut enim ad minim veniam, quis nostrud exercitation ullamco laboris nisi ut aliquip ex ea commodo consequat. Duis aute</p>
    <div class="who">Jason R., Austin</div>
    <div class="avatar" role="img" aria-label="Customer portrait"></div>
  </article>
  <article class="card" style="left:797px;top:168px">
    <div class="stars">★★★★☆</div>
    <p>Lorem ipsum dolor sit amet, consectetur adipiscing elit, sed do eiusmod tempor incididunt ut labore et dolore magna aliqua. Ut enim ad minim veniam, quis nostrud exercitation ullamco laboris nisi ut aliquip ex ea commodo consequat. Duis aute</p>
    <div class="who">Emily T., Orlando</div>
    <div class="avatar" role="img" aria-label="Customer portrait"></div>
  </article>
  <article class="card" style="left:1137px;top:220px">
    <div class="stars">★★★★☆</div>
    <p>Lorem ipsum dolor sit amet, consectetur adipiscing elit, sed do eiusmod tempor incididunt ut labore et dolore magna aliqua. Ut enim ad minim veniam, quis nostrud exercitation ullamco laboris nisi ut aliquip ex ea commodo consequat. Duis aute</p>
    <div class="who">Jhon</div>
  </article>
</section>

<section class="cta">
  <h2 class="display">Better Fit Better Score</h2>
  <p class="sub">Five minutes to a custom AI fit built from your data.</p>
  <a class="btn" href="#" style="left:460px;top:189px;width:279px;height:44px;font-size:14px">Start My Clearline Now</a>
  <p class="tag">CLEARLINE™ by VESKO GOLF · Precision Engineered. AI Perfected.</p>
</section>

<footer class="footer">Copyright 2025. Company Name. All Rights Reserved</footer>

</body>
</html>
```